Oil and Gas Exploration and Production company needs a business card design

We need a business card design using our logo and colors in the logo. We want a mainstream design.

```html
<!DOCTYPE html>
<html lang="en">
<head>
<meta charset="utf-8">
<title>Solara Oil &amp; Gas – Business Card</title>
<link href="https://fonts.googleapis.com/css2?family=Roboto+Slab:wght@700&family=Roboto:wght@400;500&display=swap" rel="stylesheet">
<style>
  :root {
    --ink: #161515;
    --card-black: #1f1d1e;
    --gold: #d09a2c;
    --paper: #ffffff;
    --stage: #7d7d7d;
    --soft-text: #e9e9e9;
  }
  html, body {
    margin: 0;
    width: 1200px;
    height: 900px;
    overflow: hidden;
    background: var(--stage);
    font-family: "Roboto", Arial, sans-serif;
  }
  .canvas {
    position: relative;
    width: 1200px;
    height: 900px;
  }
  .card {
    position: absolute;
    width: 680px;
    height: 390px;
    border-radius: 26px;
    overflow: hidden;
  }
  .card--front { left: 260px; top: 45px; background: var(--paper); }
  .card--back  { left: 260px; top: 465px; background: var(--card-black); }

  .wave { position: absolute; inset: 0; width: 680px; height: 390px; }

  .brand {
    position: absolute;
    display: flex;
    align-items: center;
    gap: 12px;
    font-family: "Roboto Slab", Georgia, serif;
    font-weight: 700;
    white-space: nowrap;
  }
  .brand__dot {
    border-radius: 50%;
    background: var(--gold);
    flex: none;
  }
  .card--front .brand { left: 40px; top: 40px; font-size: 34px; color: var(--ink); }
  .card--front .brand__dot { width: 30px; height: 30px; }
  .card--back .brand {
    left: 0; right: 0; top: 165px;
    justify-content: center;
    font-size: 46px;
    color: var(--paper);
  }
  .card--back .brand__dot { width: 42px; height: 42px; }

  .person {
    position: absolute;
    right: 40px;
    top: 160px;
    text-align: right;
  }
  .person__name { font-size: 28px; color: var(--gold); font-weight: 500; line-height: 1.1; }
  .person__role { font-size: 13px; color: var(--ink); margin-top: 4px; }

  .contact {
    position: absolute;
    right: 40px;
    top: 284px;
    text-align: right;
    font-size: 13px;
    line-height: 19px;
    color: var(--soft-text);
  }
  .contact__line { display: flex; justify-content: flex-end; align-items: center; gap: 7px; }
  .contact__accent { color: var(--gold); }
  .icon { width: 11px; height: 11px; flex: none; }
  .icon-spacer { width: 11px; flex: none; }
</style>
</head>
<body>
<main class="canvas">

  <section class="card card--front" aria-label="Business card front">
    <svg class="wave" viewBox="0 0 680 390" aria-hidden="true">
      <path fill="#d09a2c" d="M0,112 C90,122 140,212 300,222 C450,232 560,202 680,234 L680,390 L0,390 Z"/>
      <path fill="#ffffff" d="M0,128 C90,138 140,228 300,238 C450,248 560,218 680,250 L680,390 L0,390 Z"/>
      <path fill="#161515" d="M0,140 C90,150 140,240 300,250 C450,260 560,230 680,262 L680,390 L0,390 Z"/>
    </svg>

    <div class="brand"><span class="brand__dot"></span>Solara Oil &amp; Gas</div>

    <div class="person">
      <div class="person__name">Dale Hensley</div>
      <div class="person__role">CFO</div>
    </div>

    <div class="contact">
      <div class="contact__line">2450 W Ridge Ave,<span class="icon-spacer"></span></div>
      <div class="contact__line">Abilene, Texas US<span class="icon-spacer"></span></div>
      <div class="contact__line">(555) 210-4478
        <svg class="icon" viewBox="0 0 12 12" aria-hidden="true"><path fill="#d09a2c" d="M3 1l2 2.5-1.2 1.2a7 7 0 0 0 3.5 3.5L8.5 7 11 9l-1.5 2C5 11 1 7 1 2.5z"/></svg>
      </div>
      <div class="contact__line">info@solaraoilgas.com
        <svg class="icon" viewBox="0 0 12 12" aria-hidden="true"><rect x="1" y="2.5" width="10" height="7" fill="none" stroke="#d09a2c" stroke-width="1.3"/><path d="M1 2.5l5 4 5-4" fill="none" stroke="#d09a2c" stroke-width="1.3"/></svg>
      </div>
      <div class="contact__line">www.<span class="contact__accent">solaraoilgas</span>.com
        <svg class="icon" viewBox="0 0 12 12" aria-hidden="true"><circle cx="6" cy="6" r="5" fill="none" stroke="#d09a2c" stroke-width="1.2"/><path d="M1 6h10M6 1c-2.5 3-2.5 7 0 10M6 1c2.5 3 2.5 7 0 10" fill="none" stroke="#d09a2c" stroke-width="1"/></svg>
      </div>
    </div>
  </section>

  <section class="card card--back" aria-label="Business card back">
    <div class="brand"><span class="brand__dot"></span>Solara Oil &amp; Gas</div>
  </section>

</main>
</body>
</html>
```